TalkHarbor - Language Coaching Services

Sleek, innovative, trendy design for Language Coaching business.

TalkHarbor is a new UK based company that provides Language Coaching services. We offer highly personalized on-line and face to face language courses. We also impart learning techniques workshops based on the latest neuroscience research for second-language acquisition.

Target Market(s)

See attached info

Industry/Entity Type

Consulting

Contact Information for Business Card

TalkHarbor
DaniaKV@talkharbor.co.uk
TalkHarbor.co.uk
London, UK

Font styles to use
Sans Serif

```html
<!DOCTYPE html>
<html lang="en">
<head>
<meta charset="UTF-8">
<title>TalkHarbor – Business Card</title>
<link rel="stylesheet" href="https://fonts.googleapis.com/css2?family=Lato:wght@300;400;700&display=swap">
<style>
  :root {
    --bg: #1d1d1f;
    --blue-light: #2aa6c6;
    --blue-mid: #2190b8;
    --blue-deep: #19699a;
    --brand-blue: #1f7eae;
    --white: #ffffff;
    --white-faint: rgba(255, 255, 255, 0.14);
  }
  * { margin: 0; padding: 0; box-sizing: border-box; }
  html, body {
    width: 1200px; height: 900px; overflow: hidden;
    background: var(--bg);
    font-family: 'Lato', sans-serif;
  }
  .canvas { position: relative; width: 1200px; height: 900px; }

  .card {
    position: absolute;
    width: 620px; height: 354px;
    overflow: hidden;
    box-shadow: 0 14px 30px rgba(0, 0, 0, 0.45);
  }

  /* Front side */
  .card-front {
    left: 110px; top: 100px;
    background: linear-gradient(30deg, var(--blue-light) 0%, var(--blue-mid) 50%, var(--blue-deep) 100%);
  }
  .front-ring {
    position: absolute;
    left: 50%; top: 150px;
    width: 210px; height: 210px;
    transform: translate(-50%, -50%);
    border: 16px solid var(--white-faint);
    border-radius: 50%;
  }
  .front-wordmark {
    position: absolute; left: 0; right: 0; top: 122px;
    text-align: center;
    color: var(--white);
    font-weight: 400;
    font-size: 48px;
    letter-spacing: 2px;
    text-transform: uppercase;
  }
  .front-website {
    position: absolute; left: 0; right: 0; bottom: 46px;
    text-align: center;
    color: var(--white);
    font-weight: 400;
    font-size: 14px;
    letter-spacing: 6px;
  }

  /* Back side */
  .card-back {
    left: 470px; top: 470px;
    background: linear-gradient(30deg, var(--blue-light) 0%, var(--blue-mid) 55%, var(--blue-deep) 100%);
  }
  .back-circle {
    position: absolute;
    left: 330px; top: -110px;
    width: 500px; height: 500px;
    border-radius: 50%;
    background: var(--white);
  }
  .back-logo {
    position: absolute;
    left: 350px; top: 70px; width: 250px;
    display: flex; flex-direction: column; align-items: center;
  }
  .back-logo-dot {
    width: 62px; height: 62px;
    border: 6px solid var(--brand-blue);
    border-radius: 50%;
    margin-bottom: 12px;
  }
  .back-wordmark {
    color: var(--brand-blue);
    font-weight: 400;
    font-size: 30px;
    letter-spacing: 1px;
    text-transform: uppercase;
  }

  .contact {
    position: absolute;
    left: 80px; top: 150px;
    color: var(--white);
  }
  .contact-name { font-size: 16px; font-weight: 400; }
  .contact-name strong { font-weight: 700; }
  .contact-title { font-size: 11px; font-weight: 400; margin-top: 1px; }
  .contact-address {
    font-size: 13px; font-weight: 700; line-height: 1.35;
    margin-top: 20px;
  }
  .contact-list { list-style: none; margin-top: 20px; }
  .contact-item {
    display: flex; align-items: center;
    font-size: 13px; font-weight: 400;
    height: 22px;
  }
  .contact-icon { width: 17px; height: 17px; margin-right: 12px; flex: none; }
</style>
</head>
<body>
<main class="canvas">

  <section class="card card-front" aria-label="Business card front">
    <div class="front-ring" aria-hidden="true"></div>
    <div class="front-wordmark">TalkHarbor</div>
    <div class="front-website">www.TalkHarbor.co.uk</div>
  </section>

  <section class="card card-back" aria-label="Business card back">
    <div class="back-circle" aria-hidden="true"></div>
    <div class="back-logo">
      <div class="back-logo-dot" aria-hidden="true"></div>
      <div class="back-wordmark">TalkHarbor</div>
    </div>

    <div class="contact">
      <p class="contact-name">Maren <strong>Ellsworth</strong></p>
      <p class="contact-title">Chief Executive Officer</p>
      <p class="contact-address">48 Quayside Row, Suite 210<br>London, EC2A 4NE</p>
      <ul class="contact-list">
        <li class="contact-item">
          <svg class="contact-icon" viewBox="0 0 20 20" aria-hidden="true">
            <circle cx="10" cy="10" r="10" fill="#fff"/>
            <path d="M6.5 5.5c.6-.5 1.3-.4 1.7.2l.9 1.4c.3.5.2 1-.2 1.4l-.6.5c.5 1.2 1.4 2.1 2.6 2.6l.5-.6c.4-.4.9-.5 1.4-.2l1.4.9c.6.4.7 1.1.2 1.7l-.6.6c-.7.7-1.8.8-2.7.3-2-1.1-3.6-2.7-4.7-4.7-.5-.9-.4-2 .3-2.7z" fill="#2190b8"/>
          </svg>
          020.7946.0381
        </li>
        <li class="contact-item">
          <svg class="contact-icon" viewBox="0 0 20 20" aria-hidden="true">
            <circle cx="10" cy="10" r="10" fill="#fff"/>
            <rect x="7" y="5" width="6" height="3" fill="#2190b8"/>
            <rect x="5" y="8" width="10" height="5" rx="1" fill="#2190b8"/>
            <rect x="7" y="12" width="6" height="3" fill="#2190b8"/>
          </svg>
          020.7946.0729
        </li>
        <li class="contact-item">
          <svg class="contact-icon" viewBox="0 0 20 20" aria-hidden="true">
            <circle cx="10" cy="10" r="10" fill="#fff"/>
            <rect x="5" y="6.5" width="10" height="7" rx="0.8" fill="#2190b8"/>
            <path d="M5.5 7l4.5 3.5L14.5 7" fill="none" stroke="#fff" stroke-width="1"/>
          </svg>
          DaniaKV@talkharbor.co.uk
        </li>
      </ul>
    </div>
  </section>

</main>
</body>
</html>
```